Need website for LED Signs company

Need an web page for a sign company. Basic home page / Tab for photo gallery (projects), tab for other projects could be photo gallery type with the ability for descriptions gallery to be able to have albums (projects) and tab for about us / testimonials Should be easy for me to change with dreamweaver or easy to change add remove content. I will provide pictures and content I would be happy if it could be set up like a template where i can add the content after but i would provide as much content as possible the current page is http://glowcrestsigns.ca examples of my competition:https://metroled.com/led-message-signs/http://www.libertevision.com/https://www.daktronics.com/en-us/products/message-displaysSEO optimized

1 page

• I want to feature LED signs and EMC's the Special projects tab tab will or should be a photo type gallery that is easy to add photos with detailed descriptions
• I do not want to wast peoples time making something similar to what i have now.
• To help me pick a winner Please show links to some of the sites you have created in the past. .

```html
<!DOCTYPE html>
<html lang="en">
<head>
<meta charset="utf-8">
<title>Glowcrest Signs — The Future of L.E.D Technology</title>
<link rel="stylesheet" href="https://fonts.googleapis.com/css2?family=Mulish:wght@400;600;700&family=Montserrat:wght@400;600;800&display=swap">
<style>
:root{
  --black:#000;
  --ink:#333;
  --blue:#2f6fdc;
  --blue-btn:#1f6fe0;
  --red:#e3171c;
  --green:#33c13a;
  --white:#fff;
  --footer:#262626;
  --muted:#9a9a9a;
}
*{margin:0;padding:0;box-sizing:border-box}
html,body{width:1200px;height:3383px;overflow:hidden;background:var(--white)}
body{font-family:"Mulish",sans-serif;color:var(--ink);position:relative}
section,header,footer{position:absolute;left:0;width:1200px}
.abs{position:absolute}
.ph{position:absolute}

/* header */
.site-header{top:0;height:81px;background:var(--black)}
.brand{left:147px;top:20px;font-family:"Montserrat",sans-serif;font-weight:800;font-size:34px;color:var(--white);letter-spacing:-.5px}
.main-nav{right:147px;top:31px;display:flex;gap:28px;font-family:"Montserrat",sans-serif;font-size:14px;color:var(--white);text-transform:uppercase}
.main-nav .active{color:var(--green)}

/* hero */
.hero{top:81px;height:533px;background:linear-gradient(180deg,#050505,#120808 70%,#1a0a0a)}
.hero-title{width:100%;top:34px;text-align:center;font-size:34px;color:var(--blue);font-weight:400}
.hero-visual{left:350px;top:99px;width:520px;height:434px;background:radial-gradient(ellipse at 50% 45%,#ff3a24 0%,#d41a12 45%,#5a0806 80%,#140303 100%);border-radius:30px 30px 0 0}
.hero-arrow{top:250px;width:32px;height:32px;border-radius:50%;background:var(--red)}
.hero-arrow.prev{left:49px}.hero-arrow.next{left:1112px}

/* welcome */
.welcome{top:614px;height:539px;background:var(--white)}
.welcome h1{left:147px;top:76px;font-size:36px;font-weight:400;color:var(--blue)}
.welcome-copy{left:147px;top:136px;width:580px;font-size:18px;line-height:34px;color:var(--ink)}
.welcome-copy p+p{margin-top:34px}
.welcome-photo{left:758px;top:-95px;width:298px;height:553px;background:linear-gradient(180deg,#38533a 0%,#4e6b40 40%,#6b4a2a 70%,#3d5a30 100%);border:1px solid #ddd}

/* projects */
.projects{top:1153px;height:544px;background:radial-gradient(circle at 12% 20%,#1d3b6a 0,transparent 18%),radial-gradient(circle at 88% 30%,#5a1838 0,transparent 16%),radial-gradient(circle at 70% 85%,#1a4a4a 0,transparent 14%),linear-gradient(180deg,#0b1426,#141a2c)}
.section-title{width:100%;text-align:center;font-size:34px;font-weight:400;color:var(--blue)}
.projects .section-title{top:70px}
.projects-lead{width:100%;top:128px;text-align:center;font-size:19px;color:var(--white)}
.projects-sub{width:100%;top:158px;text-align:center;font-size:19px;color:var(--green)}
.project-card{top:217px;width:298px;height:241px}
.project-card .ph{left:0;top:0;width:298px;height:198px}
.project-card .btn{position:absolute;left:16px;top:184px;width:266px;height:57px;background:var(--blue-btn);color:var(--white);font-size:20px;display:flex;align-items:center;justify-content:center}
.card-a{left:144px}.card-b{left:451px}.card-c{left:758px}
.card-a .ph{background:linear-gradient(180deg,#6b7a80,#2d4a2f 60%,#3b5a33)}
.card-b .ph{background:linear-gradient(180deg,#1a1a1a,#3b3530 60%,#15120f)}
.card-c .ph{background:linear-gradient(180deg,#8a96a8,#4f6a4a 55%,#2c3a2c)}

/* gallery */
.gallery{top:1697px;height:683px;background:var(--white)}
.gallery .section-title{top:72px}
.g-tile{position:absolute}
.g1{left:144px;top:137px;width:217px;height:185px;background:linear-gradient(135deg,#4a4f7a,#c23a6a 50%,#2a3a8a)}
.g2{left:144px;top:338px;width:217px;height:185px;background:linear-gradient(135deg,#e0a030,#c0402a 45%,#2a7ab0)}
.g3{left:374px;top:137px;width:452px;height:386px;background:linear-gradient(180deg,#3a3530,#2a2622 60%,#1a1816)}
.g4{left:837px;top:137px;width:219px;height:185px;background:linear-gradient(135deg,#0a0a20,#3a4ac0 50%,#0a0a20)}
.g5{left:837px;top:338px;width:219px;height:185px;background:linear-gradient(180deg,#1a1e22,#2a3a34 50%,#1a1e22)}
.play{position:absolute;left:203px;top:170px;width:46px;height:46px}
.btn-red{position:absolute;background:var(--red);color:var(--white);font-size:16px;display:flex;align-items:center;justify-content:center;border-radius:3px}
.view-all{left:548px;top:555px;width:104px;height:47px}

/* testimonials */
.testimonials{top:2380px;height:551px;background:radial-gradient(circle at 15% 30%,#3a1010 0,transparent 20%),radial-gradient(circle at 85% 70%,#10303a 0,transparent 18%),linear-gradient(180deg,#0c0c0c,#1a1414)}
.testimonials .section-title{top:70px}
.quote-box{left:144px;top:136px;width:912px;height:295px;background:var(--white);text-align:center;padding:28px 40px 0}
.quote-box p{font-size:16px;line-height:30px;color:#555;font-family:"Open Sans","Mulish",sans-serif}
.quote-name{margin-top:24px;font-size:18px;color:var(--red)}
.quote-role{margin-top:4px;font-size:13px;color:var(--green)}
.avatar{position:absolute;border-radius:50%;background:#555;border:3px solid #2a2a2a}
.av1{left:488px;top:398px;width:63px;height:63px}
.av2{left:555px;top:386px;width:86px;height:86px;background:#333}
.av3{left:648px;top:398px;width:63px;height:63px}
.t-arrow{top:270px;width:24px;height:40px}
.t-arrow.prev{left:52px}.t-arrow.next{left:1126px}

/* contact */
.contact{top:2931px;height:340px;background:var(--white)}
.contact .section-title{top:70px}
.contact-line{width:100%;text-align:center;font-size:21px;color:var(--red);display:flex;justify-content:center;gap:30px;align-items:center}
.contact-line span{display:inline-flex;align-items:center;gap:8px}
.addr{top:127px}.reach{top:165px}
.quote-btn{left:541px;top:212px;width:118px;height:47px}

/* footer */
.site-footer{top:3271px;height:112px;background:var(--footer)}
.footer-nav{left:144px;top:31px;font-size:12px;color:#ccc;display:flex;gap:10px}
.footer-nav i{font-style:normal;color:#888}
.copyright{left:144px;top:63px;font-size:12px;color:var(--muted)}
</style>
</head>
<body>

<header class="site-header">
  <div class="abs brand">Glowcrest Signs</div>
  <nav class="abs main-nav">
    <span class="active">Home</span><span>Projects</span><span>Gallery</span><span>About Us</span><span>Contact Us</span>
  </nav>
</header>

<section class="hero">
  <h2 class="abs hero-title">The Future of L.E.D Technology</h2>
  <div class="ph hero-visual" role="img" aria-label="Illuminated red LED cube display glowing on a dark stage"></div>
  <svg class="abs hero-arrow prev" viewBox="0 0 32 32"><circle cx="16" cy="16" r="16" fill="#e3171c"/><path d="M18 10l-6 6 6 6" stroke="#000" stroke-width="3" fill="none"/></svg>
  <svg class="abs hero-arrow next" viewBox="0 0 32 32"><circle cx="16" cy="16" r="16" fill="#e3171c"/><path d="M14 10l6 6-6 6" stroke="#000" stroke-width="3" fill="none"/></svg>
</section>

<section class="welcome">
  <h1 class="abs">Welcome to Glowcrest Signs</h1>
  <div class="abs welcome-copy">
    <p>Glowcrest Signs is not your average L.E.D. Company. Our technology and custom made LED modules have what is takes to make your custom project come to life. Our team will work with you to create your wildest projects. No project is to big or to small. From digital signage, video walls, window signs or custom made DJ booths, Glowcrest Signs will exceed your expectations.</p>
    <p>Our strong manufacturing team will transform your ideas into L.E.D. works of art.</p>
  </div>
  <div class="ph welcome-photo" role="img" aria-label="Outdoor LED message sign in a timber frame among trees"></div>
</section>

<section class="projects">
  <h2 class="abs section-title">Projects</h2>
  <p class="abs projects-lead">We are a custom build service. If you can dream it, we can build it.</p>
  <p class="abs projects-sub">From outdoor displays in your back yard, to massive video walls for indoor and outdoor applications.</p>
  <div class="abs project-card card-a"><div class="ph" role="img" aria-label="Outdoor LED display sign on a lawn"></div><div class="btn">Outdoor Displays</div></div>
  <div class="abs project-card card-b"><div class="ph" role="img" aria-label="Indoor entrance with LED video wall panels"></div><div class="btn">Video Walls</div></div>
  <div class="abs project-card card-c"><div class="ph" role="img" aria-label="Backyard pool with outdoor LED screens"></div><div class="btn">Outdoor Applications</div></div>
</section>

<section class="gallery">
  <h2 class="abs section-title">Gallery</h2>
  <div class="g-tile g1" role="img" aria-label="Pair of colourful LED window displays"></div>
  <div class="g-tile g2" role="img" aria-label="Vivid artwork shown on an LED panel"></div>
  <div class="g-tile g3" role="img" aria-label="Video of an LED cube build in the workshop">
    <svg class="play" viewBox="0 0 46 46"><circle cx="23" cy="23" r="23" fill="#fff"/><path d="M18 13l14 10-14 10z" fill="#222"/></svg>
  </div>
  <div class="g-tile g4" role="img" aria-label="Glowing blue-edged LED cube display"></div>
  <div class="g-tile g5" role="img" aria-label="Scrolling LED message sign at night"></div>
  <div class="btn-red view-all">View All</div>
</section>

<section class="testimonials">
  <h2 class="abs section-title">Testimonials</h2>
  <div class="abs quote-box">
    <p>Nam fringilla nulla vel nisl condimentum, dapibus condimentum enim porta. Phasellus blandit quam a ipsum gravida dapibus. Cras sed augue tortor. Suspendisse elit ligula, iaculis dignissim justo eu, vestibulum venenatis elit. Sed egestas, nisl id cursus ultricies, turpis orci rhoncus odio, id tristique odio ex in lacus. Nam suscipit sapien eget blandit sollicitudin.</p>
    <div class="quote-name">Marcus Lindell</div>
    <div class="quote-role">Fusce porta arcu aliquet dictum nulla</div>
  </div>
  <div class="avatar av1"></div>
  <div class="avatar av2"></div>
  <div class="avatar av3"></div>
  <svg class="abs t-arrow prev" viewBox="0 0 24 40"><path d="M18 8L6 20l12 12" stroke="#fff" stroke-width="3" fill="none"/></svg>
  <svg class="abs t-arrow next" viewBox="0 0 24 40"><path d="M6 8l12 12-12 12" stroke="#fff" stroke-width="3" fill="none"/></svg>
</section>

<section class="contact">
  <h2 class="abs section-title">Contact Us</h2>
  <div class="abs contact-line addr">
    <span><svg width="14" height="20" viewBox="0 0 14 20"><path d="M7 0a7 7 0 0 0-7 7c0 5 7 13 7 13s7-8 7-13a7 7 0 0 0-7-7zm0 10a3 3 0 1 1 0-6 3 3 0 0 1 0 6z" fill="#e3171c"/></svg>Lakemoor, Saskatchewan S9Z 2R4 Canada</span>
  </div>
  <div class="abs contact-line reach">
    <span><svg width="16" height="16" viewBox="0 0 16 16"><path d="M3 1l3 3-2 2c1 2 3 4 5 5l2-2 3 3-2 3C6 15 1 10 0 3z" fill="#e3171c"/></svg>(555) 014-0220</span>
    <span><svg width="18" height="14" viewBox="0 0 18 14"><rect width="18" height="14" rx="1" fill="#e3171c"/><path d="M1 1l8 7 8-7" stroke="#fff" stroke-width="1.5" fill="none"/></svg>info@glowcrestsigns.ca</span>
  </div>
  <div class="btn-red quote-btn">Get a Quote</div>
</section>

<footer class="site-footer">
  <nav class="abs footer-nav"><span>Home</span><i>|</i><span>Projects</span><i>|</i><span>Gallery</span><i>|</i><span>About Us</span><i>|</i><span>Contact Us</span></nav>
  <div class="abs copyright">Copyright © 2019 Glowcrest Signs. All rights reserved.</div>
</footer>

</body>
</html>
```